Redesign website for small print company

Vindurgata is a small printing company in Iceland mainly servicing Students, schools, etc. We are also doing all kind of other jobs, like business cards, book printing, brochure printing etc. We are also selling books online.
Our website is: www.vindurgata.is
What we are looking for is:
- Web Design (Uncoded - PSD layout only)
- Mobile friendly design, using our current color scheme: Red, green, yellow and light gray.
- Clean simple design
- Simple, light and easy to use.
- More menu Items/drop down
Industry/Entity Type
Digital Printing
Number of Pages Required
5+ page
Requirements
Must have
- Easy navigation
- Designed for mobile
- Current color scheme (see logo)
Nice to have
- Icon based products

```html
<!DOCTYPE html>
<html lang="is">
<head>
<meta charset="utf-8">
<title>Vindurgata – Prentþjónusta</title>
<link rel="stylesheet" href="https://fonts.googleapis.com/css2?family=Montserrat:wght@500;600;700&family=Lato:wght@400;700&display=swap">
<style>
  :root {
    --red: #ee3a32;
    --red-soft: #f7c3c0;
    --yellow: #ffd200;
    --yellow-soft: #fff0a8;
    --green: #0c6130;
    --green-soft: #bfd7c8;
    --gray-light: #efefef;
    --gray-band: #ececec;
    --text-dark: #2a2a2a;
    --text-body: #555555;
    --footer-bg: #333333;
    --white: #ffffff;
  }
  * { box-sizing: border-box; margin: 0; padding: 0; }
  html, body { width: 1200px; height: 2835px; overflow: hidden; }
  body { position: relative; background: var(--white); font-family: "Lato", Arial, sans-serif; color: var(--text-body); }
  .abs { position: absolute; }

  /* Header */
  .site-header { position: absolute; left: 0; top: 0; width: 1200px; height: 90px; background: var(--gray-light); }
  .brand { position: absolute; left: 76px; top: 24px; display: flex; align-items: center; gap: 12px; }
  .brand-square { width: 38px; height: 38px; background: var(--red); }
  .brand-name { font-family: "Montserrat", Arial, sans-serif; font-weight: 700; font-size: 29px; color: var(--text-dark); letter-spacing: 0.5px; }
  .main-nav { position: absolute; top: 34px; left: 533px; display: flex; gap: 30px; font-size: 15px; text-transform: uppercase; color: #444; }
  .main-nav .active { position: relative; }
  .main-nav .active::after { content: ""; position: absolute; left: -2px; right: -2px; top: 38px; height: 3px; background: var(--red); }
  .nav-tools { position: absolute; left: 1030px; top: 31px; display: flex; align-items: center; gap: 22px; }
  .nav-divider { width: 1px; height: 26px; background: #bbb; }

  /* Hero */
  .hero { position: absolute; left: 0; top: 90px; width: 1200px; height: 496px; background: var(--gray-light); }
  .hero-title { position: absolute; left: 0; top: 176px; width: 1200px; text-align: center; font-family: "Montserrat", Arial, sans-serif; font-weight: 600; font-size: 44px; line-height: 52px; color: var(--text-dark); }
  .mockup { position: absolute; background: linear-gradient(145deg, #fafafa, #d8d8d8); box-shadow: 0 10px 20px rgba(0,0,0,0.15); }
  .laptop-screen { position: absolute; left: 394px; top: 344px; width: 412px; height: 268px; background: #2b2b2b; border-radius: 14px 14px 0 0; padding: 18px 18px 0; }
  .laptop-screen .screen-fill { width: 100%; height: 232px; background: linear-gradient(120deg, #7c8a6a 0%, #b7c0c8 45%, #4b5f78 100%); }
  .laptop-base { position: absolute; left: 321px; top: 612px; width: 558px; height: 18px; background: linear-gradient(#e6e6e6, #a9a9a9); border-radius: 0 0 40px 40px; }

  /* Action circles */
  .dots-band { position: absolute; left: 0; top: 728px; width: 1200px; height: 274px; background: radial-gradient(ellipse at center, rgba(255,255,255,0) 40%, rgba(240,240,240,0.7) 100%), linear-gradient(90deg, #fde6e4, #fff6cf, #e2efe6, #fde6e4, #e3eaf6); opacity: 0.6; }
  .action { position: absolute; top: 769px; width: 170px; height: 170px; border-radius: 50%; display: flex; align-items: center; justify-content: center; text-align: center; font-family: "Montserrat", Arial, sans-serif; font-weight: 700; font-size: 21px; line-height: 30px; color: var(--white); }
  .action-red { left: 204px; background: var(--red); box-shadow: 0 0 0 12px var(--red-soft); }
  .action-yellow { left: 514px; background: var(--yellow); box-shadow: 0 0 0 12px var(--yellow-soft); }
  .action-green { left: 824px; background: var(--green); box-shadow: 0 0 0 12px var(--green-soft); }

  /* About */
  .about-art { position: absolute; left: 75px; top: 1077px; width: 416px; height: 416px; border-radius: 50%; background: #eeeeee; }
  .about-art-fill { position: absolute; left: 140px; top: 1100px; width: 290px; height: 370px; background: linear-gradient(160deg, #f8f8f8 0%, #e0e0e0 60%, #cfcfcf 100%); transform: rotate(-4deg); }
  .section-title { font-family: "Montserrat", Arial, sans-serif; font-weight: 600; font-size: 42px; color: var(--text-dark); }
  .about-title { position: absolute; left: 586px; top: 1138px; }
  .about-text { position: absolute; left: 586px; top: 1202px; width: 545px; font-size: 14.5px; line-height: 25px; color: var(--text-body); }
  .about-text p + p { margin-top: 10px; }
  .btn-primary { position: absolute; left: 586px; top: 1385px; width: 186px; height: 46px; border-radius: 23px; background: var(--red); color: var(--white); font-family: "Montserrat", Arial, sans-serif; font-weight: 500; font-size: 18px; letter-spacing: 0.5px; display: flex; align-items: center; justify-content: center; }

  /* Products */
  .products-title { position: absolute; left: 0; top: 1576px; width: 1200px; text-align: center; }
  .product { position: absolute; width: 360px; text-align: center; }
  .product svg { display: block; margin: 0 auto; }
  .product h3 { font-family: "Montserrat", Arial, sans-serif; font-weight: 500; font-size: 25px; color: var(--text-dark); margin-top: 14px; }
  .product p { font-size: 14px; line-height: 25px; color: var(--text-body); margin-top: 8px; }

  /* Testimonials */
  .testimonials { position: absolute; left: 0; top: 2147px; width: 1200px; height: 480px; background: var(--gray-band); }
  .testimonials-title { position: absolute; left: 79px; top: 2220px; }
  .quote-mark { position: absolute; left: 79px; top: 2300px; }
  .testimonial-text { position: absolute; left: 79px; top: 2372px; width: 590px; font-size: 14.5px; line-height: 25.5px; color: var(--text-body); }
  .slider-dots { position: absolute; left: 79px; top: 2524px; display: flex; gap: 10px; }
  .slider-dots span { width: 17px; height: 17px; border-radius: 50%; border: 2px solid #777; }
  .slider-dots .current { background: #777; }
  .person-photo { position: absolute; left: 750px; top: 2113px; width: 272px; height: 514px; background: linear-gradient(180deg, #d9b89a 0%, #c9a385 25%, #1e2c48 40%, #0f1b33 100%); border-radius: 130px 130px 0 0; }

  /* Footer */
  .site-footer { position: absolute; left: 0; top: 2627px; width: 1200px; height: 208px; background: var(--footer-bg); color: var(--white); }
  .pay-cards { position: absolute; left: 507px; top: 38px; display: flex; gap: 10px; }
  .pay-card { width: 88px; height: 52px; background: #f2f2f2; border-radius: 3px; }
  .footer-nav { position: absolute; left: 0; top: 110px; width: 1200px; text-align: center; font-size: 14px; }
  .footer-nav span.sep { margin: 0 10px; }
  .copyright { position: absolute; left: 22px; top: 156px; font-size: 14px; }
  .social-dot { position: absolute; left: 1110px; top: 156px; width: 16px; height: 16px; border-radius: 50%; background: var(--white); }
</style>
</head>
<body>

<header class="site-header">
  <div class="brand"><span class="brand-square"></span><span class="brand-name">VINDURGATA</span></div>
  <nav class="main-nav">
    <span class="active">Home</span><span>Services</span><span>Job Submit</span><span>About us</span><span>Contact us</span>
  </nav>
  <div class="nav-tools">
    <svg width="24" height="24" viewBox="0 0 24 24" fill="none" stroke="#222" stroke-width="2.4"><circle cx="10" cy="10" r="7"/><line x1="15" y1="15" x2="22" y2="22"/></svg>
    <span class="nav-divider"></span>
    <svg width="22" height="24" viewBox="0 0 22 24" fill="none" stroke="#222" stroke-width="2"><rect x="2" y="8" width="18" height="14" rx="1"/><path d="M7 8V5a4 4 0 0 1 8 0v3"/></svg>
  </div>
</header>

<section class="hero">
</section>
<div class="mockup" style="left:104px;top:175px;width:180px;height:95px;transform:rotate(-22deg);background:linear-gradient(145deg,#333,#111);" role="img" aria-label="Branded business card mockups"></div>
<div class="mockup" style="left:78px;top:380px;width:148px;height:240px;" role="img" aria-label="Branded book cover mockup"></div>
<div class="mockup" style="left:850px;top:170px;width:250px;height:200px;transform:rotate(18deg);" role="img" aria-label="Branded brochure mockup"></div>
<div class="mockup" style="left:910px;top:495px;width:200px;height:90px;transform:rotate(-28deg);" role="img" aria-label="Folded card mockup"></div>
<h1 class="hero-title">Do not worry ...<br>we'll manage Þetta</h1>
<div class="laptop-screen"><div class="screen-fill" role="img" aria-label="Printing press production line"></div></div>
<div class="laptop-base"></div>

<div class="dots-band" role="img" aria-label="Soft coloured confetti dots"></div>
<div class="action action-red">SENDA<br>VERK</div>
<div class="action action-yellow">HANNA<br>VERK</div>
<div class="action action-green">FA<br>TILBOD</div>

<div class="about-art"></div>
<div class="about-art-fill" role="img" aria-label="Printed colour test sheet coming off a roller"></div>
<h2 class="section-title about-title">About us</h2>
<div class="about-text">
  <p>Vindurgata er fyrirtæki staðsett á háskólasvæðinu sem hefur sérhæft sig í að þjónusta skólafólk, ásamt því að sinna allri almennri prentun fyrir almenning.</p>
  <p>Vindurgata gefur út greinasöfn og frumsamdar kennslubækur fyrir námskeið, prentar lokaritgerðir fyrir nema, auk þess að vinna við ótalinn fjölda smærri verka fyrir nemendur, kennara og stofnanir. Má þar nefna bæklinga, skýrslur, spurningalista, nafnspjöld, bækur, OCR skönnun og fleira.</p>
</div>
<div class="btn-primary">KNOW MORE</div>

<h2 class="section-title products-title">Product List</h2>

<div class="product" style="left:60px;top:1656px;">
  <svg width="52" height="64" viewBox="0 0 52 64" fill="none" stroke="var(--yellow)" stroke-width="2.5"><path d="M4 2h32l12 12v48H4z"/><path d="M36 2v12h12"/><line x1="12" y1="26" x2="40" y2="26"/><line x1="12" y1="34" x2="40" y2="34"/><line x1="12" y1="42" x2="40" y2="42"/><line x1="12" y1="50" x2="32" y2="50"/></svg>
  <h3>Essays</h3>
  <p>Vindurgata prentar út og bindur inn ritgerðir.<br>Ritgerðir eru ýmist kiljuinnbundnar...</p>
</div>
<div class="product" style="left:420px;top:1656px;">
  <svg width="74" height="64" viewBox="0 0 74 64" fill="none" stroke="var(--yellow)" stroke-width="2.5"><rect x="2" y="8" width="70" height="50" rx="2"/><rect x="10" y="18" width="20" height="24"/><circle cx="20" cy="27" r="5"/><line x1="38" y1="22" x2="64" y2="22"/><line x1="38" y1="32" x2="64" y2="32"/><line x1="38" y1="42" x2="56" y2="42"/></svg>
  <h3>Business cards</h3>
  <p>Nafnspjöld hjá Vindurgötu er hægt að prenta í<br>öllum stærðum og gerðum, en algengast...</p>
</div>
<div class="product" style="left:780px;top:1656px;">
  <svg width="66" height="64" viewBox="0 0 66 64" fill="none" stroke="var(--yellow)" stroke-width="2.5"><path d="M2 6l20 6 22-6 20 6v48l-20-6-22 6-20-6z"/><line x1="22" y1="12" x2="22" y2="60"/><line x1="44" y1="6" x2="44" y2="54"/><line x1="28" y1="24" x2="38" y2="22"/><line x1="28" y1="32" x2="38" y2="30"/></svg>
  <h3>Leafleats</h3>
  <p>Vindurgata prentar bæklinga í öllum stærðum<br>og gerðum og á ýmsar tegundir pappírs.</p>
</div>

<div class="product" style="left:60px;top:1883px;">
  <svg width="56" height="64" viewBox="0 0 56 64" fill="none" stroke="var(--yellow)" stroke-width="2.5"><rect x="4" y="2" width="48" height="60" rx="3"/><line x1="12" y1="2" x2="12" y2="62"/><line x1="20" y1="20" x2="44" y2="20"/><line x1="20" y1="28" x2="38" y2="28"/></svg>
  <h3>Bookprinting</h3>
  <p>Vindurgata sérhæfir sig í að prenta bækur í litlu<br>upplagi, við höfum frábæran búnað til...</p>
</div>
<div class="product" style="left:420px;top:1883px;">
  <svg width="52" height="64" viewBox="0 0 52 64" fill="none" stroke="var(--yellow)" stroke-width="2.5"><rect x="6" y="6" width="40" height="52"/><line x1="2" y1="6" x2="50" y2="6"/><line x1="2" y1="58" x2="50" y2="58"/><line x1="26" y1="1" x2="26" y2="6"/></svg>
  <h3>Posters</h3>
  <p>Vindurgata prints large posters in every size<br>and shape, from small runs to big...</p>
</div>
<div class="product" style="left:780px;top:1883px;">
  <svg width="64" height="64" viewBox="0 0 64 64" fill="none" stroke="var(--yellow)" stroke-width="2.5"><rect x="6" y="4" width="50" height="14" rx="2"/><rect x="2" y="24" width="54" height="14" rx="2"/><rect x="8" y="44" width="52" height="14" rx="2"/><line x1="14" y1="11" x2="48" y2="11"/><line x1="10" y1="31" x2="44" y2="31"/><line x1="16" y1="51" x2="52" y2="51"/></svg>
  <h3>Textbooks</h3>
  <p>Vindurgata prentar út og bindur inn ritgerðir.<br>Ritgerðir eru ýmist kiljuinnbundnar...</p>
</div>

<section class="testimonials"></section>
<h2 class="section-title testimonials-title">Testimonials</h2>
<svg class="quote-mark" width="54" height="44" viewBox="0 0 54 44" fill="var(--green)"><path d="M0 44V24C0 10 8 2 22 0v8C14 10 11 15 11 22h11v22z"/><path d="M30 44V24C30 10 38 2 52 0v8C44 10 41 15 41 22h11v22z"/></svg>
<p class="testimonial-text">Lorem Ipsum is simply dummy text of the printing and typesetting industry. Lorem Ipsum has been the industry's standard dummy text ever since the 1500s, when an unknown printer took a galley of type and scrambled it to make a type specimen book. It has survived not only five centuries, but also the leap into electronic typesetting, remaining essentially unchanged.</p>
<div class="slider-dots"><span class="current"></span><span></span><span></span><span></span></div>
<div class="person-photo" role="img" aria-label="Smiling customer in a navy polo shirt with arms crossed"></div>

<footer class="site-footer">
  <div class="pay-cards"><span class="pay-card"></span><span class="pay-card"></span></div>
  <nav class="footer-nav">Home<span class="sep">|</span>Services<span class="sep">|</span>Job Submit<span class="sep">|</span>About us<span class="sep">|</span>Contact us</nav>
  <p class="copyright">©VINDURGATA- 2018. All Rights Reserved.</p>
  <span class="social-dot"></span>
</footer>

</body>
</html>
```